Salon and Spa Distributor Business Card

Need a business card. We are are distributor in the salon and spa industry. We identify with natural beauty. Need a card with:
Company Name: Petal Quarry"
Title: "President & CEO"
Address
Company Phone number
email
website
Tag Line:" The Professional Salon Source"

Industry/Entity Type

Business

Contact Information for Business Card

Name: Dov Strommen
Title: "President & CEO"
Address: 31 Harlow Ln, Bexmoor, NJ 07813
Company Phone number: 800-463-5918
email: dovstrommen@petalquarry.example
website: www.petalquarry.example

Requirements
Should not have
• No black backgrounds

```html
<!DOCTYPE html>
<html lang="en">
<head>
<meta charset="utf-8">
<title>Petal Quarry – Business Card</title>
<link href="https://fonts.googleapis.com/css2?family=Questrial&family=Montserrat:wght@700&display=swap" rel="stylesheet">
<style>
  :root {
    --page-bg: #e6e4e0;
    --card-bg: #f3f4f2;
    --brand-green: #1b6b35;
    --accent-green: #4caf3a;
    --heading-green: #1d6a33;
    --text-dark: #3a3a3a;
    --logo-white: #f1f1ec;
  }
  * { margin: 0; padding: 0; box-sizing: border-box; }
  html, body {
    width: 1200px; height: 1010px; overflow: hidden;
    background: var(--page-bg);
  }
  .card {
    position: absolute;
    left: 100px; top: 216px;
    width: 1000px; height: 578px;
    background: var(--card-bg);
    box-shadow: 0 10px 30px rgba(0,0,0,0.18);
    overflow: hidden;
  }
  .card-shapes { position: absolute; inset: 0; }
  .brand {
    position: absolute;
    left: 0; width: 470px; top: 350px;
    text-align: center;
    color: var(--logo-white);
    font-family: "Questrial", sans-serif;
  }
  .brand-name {
    font-size: 52px;
    font-weight: 400;
    letter-spacing: 0.5px;
    line-height: 1.1;
  }
  .brand-tagline {
    margin-top: 10px;
    font-size: 19px;
    letter-spacing: 1px;
  }
  .identity {
    position: absolute;
    right: 48px; top: 50px;
    text-align: right;
  }
  .identity-name {
    font-family: "Montserrat", sans-serif;
    font-weight: 700;
    font-size: 33px;
    color: var(--heading-green);
  }
  .identity-title {
    margin-top: 6px;
    font-family: "Questrial", sans-serif;
    font-size: 20px;
    color: var(--text-dark);
  }
  .contact-list {
    position: absolute;
    right: 48px; top: 362px;
    list-style: none;
    text-align: right;
    font-family: "Questrial", sans-serif;
    font-size: 24px;
    color: var(--text-dark);
  }
  .contact-item {
    display: flex; justify-content: flex-end; align-items: center;
    gap: 12px; height: 36px;
  }
  .contact-item.address { margin-top: 4px; }
  .contact-icon { width: 22px; height: 22px; flex: none; }
</style>
</head>
<body>
  <div class="card">
    <svg class="card-shapes" viewBox="0 0 1000 578" width="1000" height="578" aria-hidden="true">
      <path d="M0 0 H444 C486 70 504 170 492 300 C482 420 462 520 424 578 H0 Z" fill="var(--accent-green)"/>
      <path d="M0 0 H430 C470 70 488 170 476 300 C466 420 448 520 408 578 H0 Z" fill="var(--brand-green)"/>
    </svg>

    <div class="brand">
      <p class="brand-name">Petal Quarry</p>
      <p class="brand-tagline">The Professional Salon Source</p>
    </div>

    <div class="identity">
      <h1 class="identity-name">Dov Strommen</h1>
      <p class="identity-title">President &amp; CEO</p>
    </div>

    <ul class="contact-list">
      <li class="contact-item">800-463-5918
        <svg class="contact-icon" viewBox="0 0 24 24" aria-hidden="true"><path d="M3 9c0-3 4-5 9-5s9 2 9 5v2h-4V9H7v2H3z M6 12h12l2 8H4z" fill="var(--brand-green)"/><circle cx="12" cy="16" r="2.2" fill="var(--card-bg)"/></svg>
      </li>
      <li class="contact-item">www.petalquarry.example
        <svg class="contact-icon" viewBox="0 0 24 24" aria-hidden="true"><circle cx="12" cy="12" r="9.5" fill="none" stroke="var(--brand-green)" stroke-width="2"/><ellipse cx="12" cy="12" rx="4" ry="9.5" fill="none" stroke="var(--brand-green)" stroke-width="1.6"/><path d="M2.5 12h19M4 7h16M4 17h16" stroke="var(--brand-green)" stroke-width="1.4"/></svg>
      </li>
      <li class="contact-item">dovstrommen@petalquarry.example
        <svg class="contact-icon" viewBox="0 0 24 24" aria-hidden="true"><rect x="2" y="5" width="20" height="14" fill="var(--brand-green)"/><path d="M2 5l10 8 10-8" fill="none" stroke="var(--card-bg)" stroke-width="1.6"/></svg>
      </li>
      <li class="contact-item address">31 Harlow Ln, Bexmoor, NJ 07813</li>
    </ul>
  </div>
</body>
</html>
```